LDI Illustration Web Design

Create illustration web design company for Lumaviro Darsa Informatika (LDI). I more prefer design with illustration concept. Detail for requirement please see attach file. I'm also attach LDI logo. This logo had 2 type, 2D design and 3D design. You can chose one of them, or used both.
For the winner or had good design would be possible to private project to completeness this website
Attach file requirement is guidance for design, but any changes are welcome
Updates
Sorry, I forgot about contact. Please add menu contact. You can put this menu besides login menu or part of menu level #1, or put on some where to adjust your design. Menu contact will give pop up window to email LDI Company and Company Information (Address, Telephone, etc)
Target Market(s)
Company (Business To Business)
Industry/Entity Type
It Company
Look and feel
Each slider illustrates characteristics of the customer's brand and the style your logo design should communicate.

```html
<!DOCTYPE html>
<html lang="en">
<head>
<meta charset="utf-8">
<title>LDI — Contact</title>
<link rel="stylesheet" href="https://fonts.googleapis.com/css2?family=Roboto:wght@300;400;700&family=Arimo:wght@400;700&display=swap">
<style>
:root{
  --sky-top:#0a1f4e;
  --sky-mid:#1e4f96;
  --sky-low:#6f9bd2;
  --horizon:#c9d9ec;
  --snow:#f1f4f8;
  --snow-shade:#e3e8ef;
  --panel:rgba(24,40,86,0.92);
  --nav-text:#c9d3e3;
  --nav-sep:#8fa3c4;
  --login:#0f5fa8;
  --white:#ffffff;
  --field-border:#b7c2d4;
  --footer:#10213f;
  --footer-text:#5d6d88;
  --welcome-a:#8fc43a;
  --welcome-b:#3f7a12;
  --btn-blue:#1a8ef0;
  --btn-blue-dark:#0a6cd0;
  --subscribe-field:#5c6470;
  --logo:#a8c83a;
}
*{margin:0;padding:0;box-sizing:border-box}
html,body{width:1200px;height:1000px;overflow:hidden}
body{position:relative;font-family:"Roboto",Arial,sans-serif;background:var(--footer);color:var(--white)}

.scene{position:absolute;left:0;top:0;width:1200px;height:788px;
  background:linear-gradient(180deg,var(--sky-top) 0%,var(--sky-mid) 32%,var(--sky-low) 66%,var(--horizon) 81%,var(--snow) 86%,var(--snow) 94%,var(--snow-shade) 100%);}

.brand{position:absolute;left:20px;top:16px;display:flex;align-items:center;gap:10px}
.brand-dot{width:44px;height:44px;border-radius:50%;background:var(--logo)}
.brand-name{font-family:"Arimo",Arial,sans-serif;font-weight:700;font-size:46px;color:var(--logo);letter-spacing:1px}

.main-nav{position:absolute;top:38px;left:0;width:1200px;height:20px}
.nav-item{position:absolute;top:0;transform:translateX(-50%);font-family:"Arimo",Arial,sans-serif;font-weight:700;font-size:11.5px;letter-spacing:.4px;color:var(--nav-text);white-space:nowrap}
.nav-item.is-current{color:#e8eef8}
.nav-item.is-current::after{content:"";position:absolute;left:0;right:0;top:16px;height:3px;background:#2f8ee0}
.nav-sep{position:absolute;top:-2px;width:1px;height:19px;background:var(--nav-sep)}
.login{position:absolute;left:1095px;top:30px;width:78px;height:31px;background:linear-gradient(180deg,#1c74c4,var(--login));border:1px solid #3a8fd8;
  font-family:"Arimo",Arial,sans-serif;font-weight:700;font-size:11.5px;color:var(--white);display:flex;align-items:center;justify-content:center;letter-spacing:.4px}

.contact-panel{position:absolute;left:210px;top:134px;width:837px;height:509px;background:var(--panel)}
.contact-title{position:absolute;left:22px;top:50px;font-weight:300;font-size:37px;color:var(--white)}
.field-label{position:absolute;font-size:13.5px;color:var(--white);font-weight:400;white-space:nowrap}
.field{position:absolute;background:var(--white);border:1px solid var(--field-border);border-radius:3px}
.send-btn{position:absolute;left:616px;top:375px;width:191px;height:28px;border-radius:3px;background:linear-gradient(180deg,#f6f6f6,#c4c4c4);
  color:#333;font-size:18px;font-weight:300;display:flex;align-items:center;justify-content:center}

.company-card{position:absolute;left:41px;top:213px;font-style:normal;font-family:"Arimo",Arial,sans-serif;font-size:15px;line-height:19.5px;color:var(--white)}
.company-card .company-name{font-size:21px;line-height:22px}
.company-card .street{font-size:14px;line-height:18px}
.company-card table{border-collapse:collapse}
.company-card td{padding:0;vertical-align:top;white-space:nowrap}
.company-card td:first-child{text-align:right;padding-right:5px}

.site-footer{position:absolute;left:0;top:788px;width:1200px;height:212px;background:var(--footer)}
.welcome{position:absolute;left:405px;top:22px;width:93px;height:36px;border-radius:5px;background:linear-gradient(180deg,var(--welcome-a),var(--welcome-b));
  font-family:"Arimo",Arial,sans-serif;font-weight:700;font-size:15px;color:var(--white);display:flex;align-items:center;justify-content:center}
.intro{position:absolute;top:69px;width:216px;font-family:"Arimo",Arial,sans-serif;font-size:9.2px;line-height:11.8px;color:var(--footer-text);text-align:justify}
.learn-more{position:absolute;top:168px;width:77px;height:19px;background:linear-gradient(180deg,var(--btn-blue),var(--btn-blue-dark));
  font-family:"Arimo",Arial,sans-serif;font-size:8px;color:var(--white);display:flex;align-items:center;justify-content:center}
.subscribe-field{position:absolute;left:896px;top:184px;width:208px;height:18px;background:var(--subscribe-field);display:flex;align-items:center;gap:6px;padding-left:7px;
  font-family:"Arimo",Arial,sans-serif;font-size:7.5px;color:#d8dde4}
.subscribe-btn{position:absolute;left:1115px;top:184px;width:66px;height:18px;background:linear-gradient(180deg,var(--btn-blue),var(--btn-blue-dark));
  font-family:"Arimo",Arial,sans-serif;font-size:7.5px;color:var(--white);display:flex;align-items:center;justify-content:center}
</style>
</head>
<body>

<div class="scene" role="img" aria-label="Illustration of a snowy landscape under a blue sky, with a large cloud, a monitor, tablet and phone half buried in snow, a small mountain and scattered objects"></div>

<header>
  <div class="brand"><span class="brand-dot"></span><span class="brand-name">LDI</span></div>
  <nav class="main-nav">
    <span class="nav-item" style="left:498px">HOME</span>
    <span class="nav-sep" style="left:539px"></span>
    <span class="nav-item" style="left:590px">SERVICES</span>
    <span class="nav-sep" style="left:634px"></span>
    <span class="nav-item" style="left:683px">PRODUCT</span>
    <span class="nav-sep" style="left:728px"></span>
    <span class="nav-item" style="left:776px">CLIENTS</span>
    <span class="nav-sep" style="left:826px"></span>
    <span class="nav-item" style="left:868px">COMPANY</span>
    <span class="nav-sep" style="left:920px"></span>
    <span class="nav-item" style="left:961px">BLOG</span>
    <span class="nav-sep" style="left:997px"></span>
    <span class="nav-item is-current" style="left:1046px">CONTACT</span>
  </nav>
  <div class="login">LOGIN</div>
</header>

<section class="contact-panel">
  <h1 class="contact-title">Contact Us</h1>

  <span class="field-label" style="right:286px;top:83px">Name:</span>
  <div class="field" style="left:558px;top:75px;width:249px;height:29px"></div>
  <span class="field-label" style="right:286px;top:117px">Your Email Address:</span>
  <div class="field" style="left:558px;top:110px;width:249px;height:29px"></div>

  <span class="field-label" style="left:331px;top:197px">Message to send to Company Name:</span>
  <div class="field" style="left:324px;top:216px;width:483px;height:151px"></div>
  <div class="send-btn">Send Message</div>

  <address class="company-card">
    <div class="company-name">LDI</div>
    <div class="street">xxx xxxxx st.</div>
    <div>City, Country, zip code</div>
    <table>
      <tr><td>Phone:</td><td>+X XXX XXXXXXX</td></tr>
      <tr><td></td><td>+X XXX XXXXXXX</td></tr>
      <tr><td></td><td>+X XXX XXXXXXX</td></tr>
      <tr><td>Fax:</td><td>+X XXX XXXXXXX</td></tr>
      <tr><td>E-mail:</td><td>name@sitename.xxx</td></tr>
    </table>
  </address>
</section>

<footer class="site-footer">
  <div class="welcome">Welcome!</div>
  <p class="intro" style="left:406px">Lorem ipsum badama dolor sit amet, consectetur adipisicing elit, sed do eiusmod tempor incididunt ut labore et dolore magna aliqua. Ut enim ad minim veniam, quis nostrud exercitation ullamco laboris nisi ut aliquip ex ea commodo consequat. Duis aute irure dolor in reprehenderit in voluptate velit esse cillum dolore eu.</p>
  <p class="intro" style="left:632px">Lorem ipsum badama dolor sit amet, consectetur adipisicing elit, sed do eiusmod tempor incididunt ut labore et dolore magna aliqua. Ut enim ad minim veniam, quis nostrud exercitation ullamco laboris nisi ut aliquip ex ea commodo consequat. Duis aute irure dolor in reprehenderit in voluptate velit esse cillum dolore eu.</p>
  <div class="learn-more" style="left:406px">LEARN MORE</div>
  <div class="learn-more" style="left:632px">LEARN MORE</div>
  <div class="subscribe-field">
    <svg width="12" height="9" viewBox="0 0 12 9" aria-hidden="true"><rect x="0.5" y="0.5" width="11" height="8" fill="none" stroke="#e6e9ee"/><path d="M0.5 0.5 L6 5 L11.5 0.5" fill="none" stroke="#e6e9ee"/></svg>
    <span>your email address...</span>
  </div>
  <div class="subscribe-btn">SUBSCRIBE</div>
</footer>

</body>
</html>
```